Business card design for a dynamic IT consulting company

We need a business card design for a young firm, specialized in the Telecommunications/Consulting industry. The name of the company is Quindor and Partners Business Consulting Ltd. (Short name: Quindor and Partnes)
Quindor = solve read reverse, so we aim to be uncomplicated and solution-oriented. The small pipe in our logo is also related to the word solve. So we need a new business card design, which is simple, eye catching and something non traditional (I would probably prefer a square shaped design rather than a rectangle, but open for suggestions). Attached our logo.

Target Market(s)

Usually our customers are Tier1 Telecoms providers (Q-Netra, Palorix, etc) and their executives.

Industry/Entity Type

Business

Contact Information for Business Card

Name: Bence Tolnavari
Email: b.tolnavari@quindor.hu
Web: www.quindor.hu
Mobile: +36 30 518 2769
Title: Managing Director

Optional:
Company name: Quindor and Partners Ltd.
Address: 1087 Budapest, Tolvenka str. 28/C, Hungary

Font styles to use
Other font styles liked:
• helveticaneue_medium, Prime Regular are used now.

Colors

Designer to choose colors to be used in the design.

Requirements
Must have
• I would like to have a 2 sided design.
Nice to have
• I thought if we make the logo a bit bigger (without the company name), that could go to the back with the company name below. I though, if the pipe in the logo is somehow touchable on the business card, would be nice and unique.

```html
<!DOCTYPE html>
<html lang="en">
<head>
<meta charset="utf-8">
<title>Quindor and Partners – Business Card</title>
<link href="https://fonts.googleapis.com/css2?family=Arimo:wght@400;700&display=swap" rel="stylesheet">
<style>
  :root {
    --backdrop: #584634;
    --card: #f4f4f4;
    --header: #5a5a5c;
    --accent-blue: #1a95d3;
    --accent-magenta: #b52a8c;
    --ink: #505052;
    --white: #ffffff;
  }
  * { box-sizing: border-box; margin: 0; padding: 0; }
  html, body {
    width: 1200px;
    height: 960px;
    overflow: hidden;
    background: var(--backdrop);
    font-family: "Arimo", Arial, sans-serif;
  }
  .card {
    position: absolute;
    top: 309px;
    width: 342px;
    height: 343px;
    background: var(--card);
    overflow: hidden;
  }
  .card--front { left: 235px; }
  .card--back { left: 623px; }

  .front-header {
    height: 90px;
    background: var(--header);
    text-align: center;
    padding-top: 28px;
  }
  .holder-name {
    color: var(--accent-blue);
    font-weight: 700;
    font-size: 19px;
    letter-spacing: -0.2px;
    line-height: 20px;
  }
  .holder-title {
    color: var(--white);
    font-size: 15px;
    line-height: 20px;
  }
  .header-rule {
    height: 1px;
    margin-top: 2px;
  }
  .header-rule--blue { background: var(--accent-blue); }
  .header-rule--magenta { background: var(--accent-magenta); }

  .company-address {
    margin-top: 43px;
    text-align: center;
    color: var(--ink);
    font-size: 14px;
    line-height: 18.5px;
  }
  .contact-list {
    margin-top: 10px;
    text-align: center;
    color: var(--ink);
    font-size: 14px;
    line-height: 18px;
    list-style: none;
  }
  .contact-label {
    color: var(--accent-blue);
    font-weight: 700;
  }
  .brand-line {
    position: absolute;
    left: 0;
    right: 0;
    top: 273px;
    display: flex;
    justify-content: center;
    align-items: center;
    gap: 10px;
  }
  .brand-square {
    width: 12px;
    height: 12px;
    background: var(--accent-magenta);
  }
  .brand-name {
    color: var(--ink);
    font-size: 24px;
    line-height: 28px;
  }

  .back-brand {
    position: absolute;
    right: 32px;
    top: 256px;
    display: flex;
    align-items: center;
    gap: 9px;
  }
  .back-brand .brand-square { background: var(--accent-blue); }
  .back-brand .brand-name { font-size: 26px; }
  .web-address {
    position: absolute;
    right: 32px;
    top: 300px;
    color: var(--ink);
    font-size: 14px;
  }
</style>
</head>
<body>
  <section class="card card--front">
    <header class="front-header">
      <h1 class="holder-name">BENCE TOLNAVARI</h1>
      <p class="holder-title">MANAGING DIRECTOR</p>
    </header>
    <div class="header-rule header-rule--blue"></div>
    <div class="header-rule header-rule--magenta"></div>
    <address class="company-address" style="font-style: normal;">
      Quindor and Partners Ltd.<br>
      1087 Budapest<br>
      Tolvenka str. 28/C, Hungary
    </address>
    <ul class="contact-list">
      <li><span class="contact-label">P:</span> +36 30 518 2769</li>
      <li><span class="contact-label">E:</span> b.tolnavari@quindor.hu</li>
    </ul>
    <div class="brand-line">
      <span class="brand-square"></span>
      <span class="brand-name">Quindor &amp; Partners</span>
    </div>
  </section>

  <section class="card card--back">
    <div class="back-brand">
      <span class="brand-square"></span>
      <span class="brand-name">Quindor</span>
    </div>
    <p class="web-address">www.quindor.hu</p>
  </section>
</body>
</html>
```